jQuery Mobile CSS for web app

Task Outline:
Create jQuery Mobile themeroller compliant CSS and icons for a mobile web app.
Task Description:
Brindle Solutions are in the process of implementing a new, web based version of their Tessel operations platform.
The web based version of Tessel is built on top of the jQuery Mobile platform and we are looking for a designer to create a jQuery Mobile themeroller compliant CSS theme pack that we can plug into our application. The aim is to remove the standard jQuery Mobile look and feel and to introduce the Brindle branding throughout the new web app.
A number of screenshots are shown in the attached design spec (brindle_solutions.pdf) that show what the current (Windows Mobile 6.5) application looks like, alongside the development version of our new web app.
Deliverables:
• jQuery Mobile (v 1.4.2) themeroller compliant CSS which provides theming for all jQuery Mobile UI components.
• Example html showing how to use the CSS theme (especially where additional html/css classes are required).
• New set of status icons (as listed in attachment)
Inspiration:
See our website for current branding: www.brindle-solutions-demo.net

```html
<!DOCTYPE html>
<html lang="en">
<head>
<meta charset="utf-8">
<title>Brindle Tessel – Home</title>
<link href="https://fonts.googleapis.com/css2?family=Open+Sans:wght@400;600;700&display=swap" rel="stylesheet">
<style>
  :root {
    --screen-bg: #000000;
    --status-bg: #3a3a3a;
    --status-text: #ffffff;
    --brand-red: #d90b0b;
    --brand-red-dark: #b80000;
    --label: #ffffff;
    --icon: #ffffff;
    --orange-top: #ffc21a; --orange-bottom: #ff7a00;
    --red-top: #ef2b2b;    --red-bottom: #a80404;
    --green-top: #35d62f;  --green-bottom: #0b8a0b;
    --blue-top: #2f7cf2;   --blue-bottom: #0a3aa8;
    --purple-top: #a43ad8; --purple-bottom: #560c94;
    --yellow-top: #ffd91a; --yellow-bottom: #f2a200;
    --cyan-top: #3fe0f8;   --cyan-bottom: #0a92cc;
    --lime-top: #b3dd26;   --lime-bottom: #5c9400;
  }
  * { box-sizing: border-box; margin: 0; padding: 0; }
  html, body {
    width: 853px; height: 1200px; overflow: hidden;
    background: var(--screen-bg);
    font-family: "Open Sans", Arial, sans-serif;
  }
  .app { width: 853px; height: 1200px; position: relative; overflow: hidden; }

  .status-bar {
    height: 45px; background: var(--status-bg); color: var(--status-text);
    display: flex; align-items: center; justify-content: space-between;
    padding: 0 16px; font-size: 20px;
  }
  .status-signal, .status-battery { display: flex; align-items: center; gap: 8px; }

  .app-header {
    height: 136px;
    background: linear-gradient(180deg, var(--brand-red) 0%, var(--brand-red-dark) 100%);
    display: flex; align-items: center; justify-content: center;
  }
  .app-title { color: #fff; font-size: 56px; font-weight: 600; letter-spacing: 0.5px; line-height: 1; }

  .launcher {
    display: grid;
    grid-template-columns: repeat(3, 212px);
    column-gap: 58px; row-gap: 52px;
    padding: 100px 0 0 52px;
  }
  .launcher-item { display: flex; flex-direction: column; align-items: center; }
  .tile {
    width: 212px; height: 196px; border-radius: 12px;
    display: flex; align-items: center; justify-content: center;
    border: 4px solid rgba(255,255,255,0.18);
    box-shadow: inset 0 -8px 14px rgba(0,0,0,0.25);
  }
  .tile svg { width: 112px; height: 112px; }
  .tile--orange { background: linear-gradient(180deg, var(--orange-top), var(--orange-bottom)); }
  .tile--red    { background: linear-gradient(180deg, var(--red-top), var(--red-bottom)); }
  .tile--green  { background: linear-gradient(180deg, var(--green-top), var(--green-bottom)); }
  .tile--blue   { background: linear-gradient(180deg, var(--blue-top), var(--blue-bottom)); }
  .tile--purple { background: linear-gradient(180deg, var(--purple-top), var(--purple-bottom)); }
  .tile--yellow { background: linear-gradient(180deg, var(--yellow-top), var(--yellow-bottom)); }
  .tile--cyan   { background: linear-gradient(180deg, var(--cyan-top), var(--cyan-bottom)); }
  .tile--lime   { background: linear-gradient(180deg, var(--lime-top), var(--lime-bottom)); }
  .icon-placeholder {
    width: 112px; height: 112px; border-radius: 10px;
    background: linear-gradient(180deg, rgba(255,255,255,0.85), rgba(255,255,255,0.55));
  }
  .tile-label {
    color: var(--label); font-size: 33px; line-height: 40px;
    margin-top: 14px; white-space: nowrap;
  }
</style>
</head>
<body>
<main class="app">
  <div class="status-bar">
    <div class="status-signal">
      <svg width="34" height="18" viewBox="0 0 34 18"><g fill="#fff"><rect x="0" y="13" width="5" height="5"/><rect x="7" y="10" width="5" height="8"/><rect x="14" y="6" width="5" height="12"/><rect x="21" y="3" width="5" height="15"/><rect x="28" y="0" width="5" height="18"/></g></svg>
      <span>3G</span>
    </div>
    <span class="status-time">8:33 PM</span>
    <div class="status-battery">
      <span>99%</span>
      <svg width="48" height="22" viewBox="0 0 48 22"><rect x="1" y="1" width="42" height="20" rx="3" fill="none" stroke="#fff" stroke-width="2"/><rect x="4" y="4" width="36" height="14" fill="#fff"/><rect x="44" y="7" width="3" height="8" fill="#fff"/></svg>
    </div>
  </div>

  <header class="app-header">
    <h1 class="app-title">Brindle Tessel</h1>
  </header>

  <nav class="launcher">
    <div class="launcher-item">
      <div class="tile tile--orange">
        <svg viewBox="0 0 100 100"><g fill="none" stroke="var(--icon)" stroke-width="6" stroke-linejoin="round"><path d="M38 28v-8h24v8"/><rect x="14" y="28" width="72" height="52" rx="6"/><path d="M14 50h72"/></g><rect x="43" y="44" width="14" height="12" fill="var(--icon)"/></svg>
      </div>
      <span class="tile-label">My Work</span>
    </div>
    <div class="launcher-item">
      <div class="tile tile--red">
        <div class="icon-placeholder" role="img" aria-label="New job icon: white figure of a person in a suit and tie"></div>
      </div>
      <span class="tile-label">New Job</span>
    </div>
    <div class="launcher-item">
      <div class="tile tile--green">
        <svg viewBox="0 0 100 100"><g fill="none" stroke="var(--icon)" stroke-width="5" stroke-linejoin="round"><path d="M38 10h24l-6 14H44z"/><path d="M44 24l-10 50 16 16 16-16-10-50"/><path d="M40 46l22-10M38 62l26-12"/></g></svg>
      </div>
      <span class="tile-label">Field</span>
    </div>
    <div class="launcher-item">
      <div class="tile tile--blue">
        <svg viewBox="0 0 100 100"><rect x="18" y="12" width="64" height="76" rx="6" fill="none" stroke="var(--icon)" stroke-width="6"/><g fill="var(--icon)"><rect x="30" y="30" width="6" height="6"/><rect x="42" y="30" width="28" height="6"/><rect x="30" y="44" width="6" height="6"/><rect x="42" y="44" width="28" height="6"/><rect x="30" y="58" width="6" height="6"/><rect x="42" y="58" width="28" height="6"/><rect x="30" y="72" width="6" height="6"/><rect x="42" y="72" width="28" height="6"/></g></svg>
      </div>
      <span class="tile-label">Timesheet</span>
    </div>
    <div class="launcher-item">
      <div class="tile tile--purple">
        <svg viewBox="0 0 100 100"><path fill="var(--icon)" d="M44 8h12l2 12 9 4 10-7 8 8-7 10 4 9 12 2v12l-12 2-4 9 7 10-8 8-10-7-9 4-2 12H44l-2-12-9-4-10 7-8-8 7-10-4-9-12-2V44l12-2 4-9-7-10 8-8 10 7 9-4z"/><circle cx="50" cy="50" r="16" fill="var(--purple-bottom)"/></svg>
      </div>
      <span class="tile-label">Authorisation</span>
    </div>
    <div class="launcher-item">
      <div class="tile tile--yellow">
        <svg viewBox="0 0 100 100"><circle cx="50" cy="50" r="28" fill="none" stroke="var(--icon)" stroke-width="20" stroke-dasharray="52 6 40 6 48 6 18 0"/></svg>
      </div>
      <span class="tile-label">Asset</span>
    </div>
    <div class="launcher-item">
      <div class="tile tile--cyan">
        <svg viewBox="0 0 100 100"><path d="M54 14h30v30L44 84 14 54z" fill="var(--icon)" stroke="var(--icon)" stroke-width="4" stroke-linejoin="round"/><circle cx="70" cy="28" r="6" fill="var(--cyan-bottom)"/></svg>
      </div>
      <span class="tile-label">Tag it</span>
    </div>
    <div class="launcher-item">
      <div class="tile tile--lime">
        <svg viewBox="0 0 100 100"><rect x="20" y="14" width="60" height="76" rx="5" fill="none" stroke="var(--icon)" stroke-width="5"/><rect x="38" y="8" width="24" height="12" rx="3" fill="var(--icon)"/><g fill="none" stroke="var(--icon)" stroke-width="4"><path d="M29 36l4 4 7-8M29 52l4 4 7-8M29 68l4 4 7-8"/></g><g fill="var(--icon)"><rect x="46" y="34" width="24" height="5"/><rect x="46" y="50" width="24" height="5"/><rect x="46" y="66" width="24" height="5"/></g></svg>
      </div>
      <span class="tile-label">From Test</span>
    </div>
  </nav>
</main>
</body>
</html>
```